The Warden's Wedding invitations

Looking for wedding invitations with at least 3 pictures of us on one side and one picture on the other side, Something romantic. Need 100 invitations 5x7 matte with envelopes. This is for a lesbian wedding. Want it to be catchy, modern yet romantic. I've given a few pictures. I trust you'll select the right ones for the project. I've enclosed some invitations I saw online. I do like the one wit 3 pics on one side, but our pics don't match the way theirs did.

Target Market(s)

Wedding guest

Font styles to use
Script

Colors

Designer to choose colors to be used in the design.

Requirements
Must have
• Marla & Tessa
• soon to be THE WARDEN'S (front side 3 pictures)
• Marlena Fairbrook & Tessa Warden (back side- 1 picture)
• HAPPILY INVITE YOU TO
• CELEBRATE
• THEIR WEDDING
• 10/13/2018 5pm at:
• Lumo Lounge:
• 4812 Quarrow Ave
• Brookhaven, Ca 92614
Should not have
• .

```html
<!DOCTYPE html>
<html lang="en">
<head>
<meta charset="utf-8">
<title>The Warden's Wedding Invitations</title>
<link rel="stylesheet" href="https://fonts.googleapis.com/css2?family=Alex+Brush&family=Pinyon+Script&family=Roboto:wght@300;700&family=Cormorant+Garamond:wght@500&display=swap">
<style>
  :root {
    --stage: #dcdde0;
    --night: #17203a;
    --night-deep: #10172c;
    --gold-light: #fbf1cf;
    --gold: #d9b56a;
    --white: #ffffff;
    --rose: #d2506a;
    --glow: rgba(255, 236, 200, 0.55);
    --lace: rgba(200, 200, 215, 0.35);
    --photo-a: #7a6a62;
    --photo-b: #c9a58f;
  }
  * { margin: 0; padding: 0; box-sizing: border-box; }
  html, body { width: 1200px; height: 1200px; overflow: hidden; }
  body { background: var(--stage); position: relative; font-family: "Roboto", sans-serif; }

  .card {
    position: absolute;
    overflow: hidden;
    background:
      radial-gradient(ellipse at 60% 45%, rgba(58, 36, 80, 0.55), transparent 60%),
      linear-gradient(170deg, var(--night) 0%, var(--night-deep) 100%);
    box-shadow: 0 8px 18px rgba(0, 0, 0, 0.35);
  }
  .card--front { left: 62px; top: 72px; width: 530px; height: 742px; }
  .card--back { left: 618px; top: 405px; width: 536px; height: 750px; }

  .string-lights {
    position: absolute; left: 0; top: 0; width: 100%; height: 300px;
    background:
      radial-gradient(circle at 63% 24%, rgba(255, 240, 210, 0.75) 0, transparent 8%),
      radial-gradient(ellipse at 55% 20%, var(--glow), transparent 55%);
    opacity: 0.6;
  }
  .card--back .string-lights { height: 260px; }

  .lace { position: absolute; bottom: 0; width: 220px; height: 230px; }
  .lace--left { left: 0; background: radial-gradient(ellipse at 0% 100%, var(--lace), transparent 70%); }
  .lace--right { right: 0; background: radial-gradient(ellipse at 100% 100%, var(--lace), transparent 70%); }

  .photo-heart { position: absolute; }
  .photo-heart svg { width: 100%; height: 100%; display: block; }

  .photo-cutout {
    position: absolute; left: 174px; top: 456px; width: 208px; height: 286px;
    border-radius: 40px 40px 0 0;
    background: linear-gradient(180deg, var(--photo-a), var(--photo-b) 60%, #e9e2da);
    opacity: 0.9;
  }

  .centered { position: absolute; left: 0; width: 100%; text-align: center; white-space: nowrap; }

  .event-title {
    position: absolute; left: 166px; width: 200px; text-align: center;
    font-family: "Pinyon Script", cursive;
    color: var(--white);
    text-shadow: 0 2px 3px rgba(0, 0, 0, 0.6);
    line-height: 1; white-space: nowrap;
  }
  .event-title--family { top: 126px; font-size: 34px; }
  .event-title--wedding { top: 166px; font-size: 42px; color: var(--gold-light); }

  .glow-rule {
    position: absolute; height: 2px;
    background: linear-gradient(90deg, transparent, #ffd9e0, transparent);
    box-shadow: 0 0 6px #ff9fb2;
  }

  .invitations-label { top: 226px; left: 20px; font-weight: 300; font-size: 38px; letter-spacing: 2px; color: var(--white); }

  .gold-script {
    font-family: "Alex Brush", cursive;
    background: linear-gradient(180deg, var(--gold-light) 20%, var(--gold) 80%);
    -webkit-background-clip: text; background-clip: text;
    color: transparent;
    filter: drop-shadow(1px 3px 1px rgba(0, 0, 0, 0.7));
    line-height: 1.1; white-space: nowrap;
  }

  .couple-names { position: absolute; top: 276px; left: 0; width: 100%; height: 110px; }
  .couple-names .gold-script { position: absolute; font-size: 78px; }
  .couple-names .name-first { right: 300px; top: 0; }
  .couple-names .name-second { left: 296px; top: 10px; }

  .amp-heart { position: absolute; }
  .amp-heart svg { width: 100%; height: 100%; display: block; }

  .event-date { top: 386px; left: 20px; font-family: "Cormorant Garamond", serif; font-weight: 500; font-size: 28px; letter-spacing: 1px; font-variant-numeric: lining-nums; color: var(--white); }
  .event-venue { top: 424px; left: 20px; font-weight: 700; font-size: 13px; color: var(--white); }

  .full-names { position: absolute; left: 0; top: 0; width: 100%; height: 360px; }
  .full-names .gold-script { position: absolute; font-size: 60px; transform: rotate(-9deg); transform-origin: left center; }
  .full-names .line-one { left: 24px; top: 160px; }
  .full-names .line-two { left: 96px; top: 262px; }

  .invite-bold { font-weight: 700; font-size: 18px; color: var(--white); }
  .invite-line-one { top: 591px; }
  .invite-celebrate { top: 621px; font-weight: 300; font-size: 31px; letter-spacing: 1px; color: var(--white); }
  .invite-line-three { top: 661px; }
</style>
</head>
<body>

<section class="card card--front">
  <div class="string-lights" role="img" aria-label="Glowing string lights across the night sky"></div>
  <div class="lace lace--left" role="img" aria-label="Lace ornament in the lower left corner"></div>
  <div class="lace lace--right" role="img" aria-label="Lace ornament in the lower right corner"></div>

  <div class="photo-heart" style="left:28px;top:36px;width:144px;height:140px;transform:rotate(-12deg)">
    <svg viewBox="0 0 100 92" role="img" aria-label="Heart-shaped photo of the couple sharing a kiss">
      <defs><linearGradient id="ph1" x1="0" y1="0" x2="1" y2="1"><stop offset="0" stop-color="#6e7a5a"/><stop offset="1" stop-color="#c49a80"/></linearGradient></defs>
      <path d="M50 90 C20 68 2 50 2 28 C2 12 14 2 28 2 C38 2 46 8 50 16 C54 8 62 2 72 2 C86 2 98 12 98 28 C98 50 80 68 50 90Z" fill="url(#ph1)" stroke="#fff" stroke-width="2"/>
    </svg>
  </div>
  <div class="photo-heart" style="left:356px;top:24px;width:142px;height:138px;transform:rotate(8deg)">
    <svg viewBox="0 0 100 92" role="img" aria-label="Heart-shaped photo of the couple smiling together">
      <defs><linearGradient id="ph2" x1="0" y1="0" x2="1" y2="1"><stop offset="0" stop-color="#8a6a58"/><stop offset="1" stop-color="#d8b29a"/></linearGradient></defs>
      <path d="M50 90 C20 68 2 50 2 28 C2 12 14 2 28 2 C38 2 46 8 50 16 C54 8 62 2 72 2 C86 2 98 12 98 28 C98 50 80 68 50 90Z" fill="url(#ph2)" stroke="#fff" stroke-width="2"/>
    </svg>
  </div>

  <p class="event-title event-title--family">The Warden's</p>
  <p class="event-title event-title--wedding">Wedding</p>
  <div class="glow-rule" style="left:196px;top:216px;width:140px"></div>
  <p class="centered invitations-label">INVITATIONS</p>

  <div class="couple-names">
    <span class="gold-script name-first">Marla</span>
    <span class="gold-script name-second">Tessa</span>
    <div class="amp-heart" style="left:236px;top:34px;width:56px;height:52px">
      <svg viewBox="0 0 100 92"><path d="M50 90 C20 68 2 50 2 28 C2 12 14 2 28 2 C38 2 46 8 50 16 C54 8 62 2 72 2 C86 2 98 12 98 28 C98 50 80 68 50 90Z" fill="var(--rose)"/><text x="50" y="54" text-anchor="middle" font-family="Alex Brush, cursive" font-size="34" fill="#fff">&amp;</text></svg>
    </div>
  </div>

  <p class="centered event-date">10/13/2018, 5pm at:</p>
  <p class="centered event-venue">Lumo Lounge: - 4812 Quarrow Ave- Brookhaven, Ca 92614</p>

  <div class="photo-cutout" role="img" aria-label="Photo of the couple holding up an 'I said yes' sign"></div>
</section>

<section class="card card--back">
  <div class="string-lights" role="img" aria-label="Glowing string lights across the night sky"></div>
  <div class="lace lace--left" role="img" aria-label="Lace ornament in the lower left corner"></div>
  <div class="lace lace--right" role="img" aria-label="Lace ornament in the lower right corner"></div>

  <div class="full-names">
    <span class="gold-script line-one">Marlena Fairbrook</span>
    <span class="gold-script line-two">Tessa Warden</span>
    <div class="amp-heart" style="left:206px;top:190px;width:70px;height:64px">
      <svg viewBox="0 0 100 92"><path d="M50 90 C20 68 2 50 2 28 C2 12 14 2 28 2 C38 2 46 8 50 16 C54 8 62 2 72 2 C86 2 98 12 98 28 C98 50 80 68 50 90Z" fill="var(--rose)"/><text x="50" y="54" text-anchor="middle" font-family="Alex Brush, cursive" font-size="34" fill="#fff">&amp;</text></svg>
    </div>
  </div>

  <div class="photo-heart" style="left:170px;top:383px;width:184px;height:176px">
    <svg viewBox="0 0 100 92" role="img" aria-label="Heart-shaped photo of the couple standing side by side">
      <defs><linearGradient id="ph3" x1="0" y1="0" x2="1" y2="1"><stop offset="0" stop-color="#c9b7a8"/><stop offset="0.6" stop-color="#7a5c4c"/><stop offset="1" stop-color="#2f7fa8"/></linearGradient></defs>
      <path d="M50 90 C20 68 2 50 2 28 C2 12 14 2 28 2 C38 2 46 8 50 16 C54 8 62 2 72 2 C86 2 98 12 98 28 C98 50 80 68 50 90Z" fill="url(#ph3)"/>
    </svg>
  </div>

  <p class="centered invite-bold invite-line-one">HAPPILY INVITE YOU TO</p>
  <p class="centered invite-celebrate">CELEBRATE</p>
  <p class="centered invite-bold invite-line-three">THEIR WEDDING</p>

  <div class="glow-rule" style="left:168px;top:711px;width:200px"></div>
  <div class="amp-heart" style="left:258px;top:703px;width:18px;height:17px">
    <svg viewBox="0 0 100 92"><path d="M50 90 C20 68 2 50 2 28 C2 12 14 2 28 2 C38 2 46 8 50 16 C54 8 62 2 72 2 C86 2 98 12 98 28 C98 50 80 68 50 90Z" fill="var(--rose)"/></svg>
  </div>
</section>

</body>
</html>
```